i need a business card for a plumbing company in california

we are a drain cleaning , maintenance plumbing company who is starting new marketing campaign for a tatrench-less pipe installation department .

Target Market(s)

the professional who appreciates time and quality workmanship.

Industry/Entity Type

Plumbing

Colors
0655a3
ec1f27

Requirements
Must have
• the second logo needs to be included
Nice to have
• a focus on the services offered
Should not have
• any underlined words on the brief

```html
<!DOCTYPE html>
<html lang="en">
<head>
<meta charset="utf-8">
<title>Keystone Plumbing — Business Card</title>
<link rel="stylesheet" href="https://fonts.googleapis.com/css2?family=Arimo:wght@400;700&display=swap">
<style>
  :root {
    --backdrop: #2a2a2c;
    --card-white: #ffffff;
    --card-shade: #eceef0;
    --brand-blue: #0655a3;
    --deep-blue: #0a3f7e;
    --brand-red: #ec1f27;
    --logo-grey: #6d6c66;
    --text-white: #ffffff;
  }
  * { margin: 0; padding: 0; box-sizing: border-box; }
  html, body {
    width: 1200px;
    height: 997px;
    overflow: hidden;
    background: var(--backdrop);
    font-family: "Arimo", Arial, sans-serif;
  }
  .stage { position: relative; width: 1200px; height: 997px; }
  .card {
    position: absolute;
    width: 520px;
    height: 297px;
    border-radius: 14px;
    overflow: hidden;
    box-shadow: 0 18px 40px rgba(0,0,0,0.55);
  }
  .card--services { left: 70px; top: 150px; }
  .card--contact { left: 610px; top: 470px; }
  .card svg { display: block; }
  .wordmark { font-family: "Arimo", Arial, sans-serif; font-weight: 700; fill: var(--logo-grey); }
  .services-line { font-size: 11.5px; letter-spacing: 0.6px; fill: var(--text-white); }
  .person-name { font-weight: 700; font-size: 15px; fill: var(--brand-red); letter-spacing: 0.4px; }
  .person-role { font-size: 13px; fill: var(--text-white); }
  .contact-line { font-size: 13px; fill: var(--text-white); }
  .contact-web { font-size: 13px; font-weight: 700; fill: var(--brand-red); letter-spacing: 0.5px; }
</style>
</head>
<body>
<main class="stage">

  <!-- Services side -->
  <section class="card card--services">
    <svg width="520" height="297" viewBox="0 0 520 297" aria-label="Card front with services">
      <defs>
        <linearGradient id="paper" x1="0" y1="0" x2="0" y2="1">
          <stop offset="0" stop-color="var(--card-white)"/>
          <stop offset="1" stop-color="var(--card-shade)"/>
        </linearGradient>
        <path id="services-curve" d="M10,275 C130,268 230,225 310,188 C390,150 450,135 515,130"/>
      </defs>
      <rect width="520" height="297" fill="url(#paper)"/>
      <path class="band-red" fill="var(--brand-red)" d="M0,297 L0,215 C120,232 220,192 300,152 C380,112 450,92 520,87 L520,297 Z"/>
      <path class="band-gap" fill="var(--card-white)" d="M0,297 L0,228 C120,244 220,204 300,164 C380,124 450,104 520,99 L520,297 Z"/>
      <path class="band-blue" fill="var(--brand-blue)" d="M0,297 L0,234 C120,250 220,210 300,170 C380,130 450,110 520,105 L520,297 Z"/>
      <g class="logo">
        <circle cx="372" cy="70" r="9" fill="var(--brand-red)"/>
        <text class="wordmark" x="130" y="86" font-size="36">Keystone</text>
        <text class="wordmark" x="170" y="124" font-size="36">Plumbing</text>
      </g>
      <text class="services-line"><textPath href="#services-curve" startOffset="4%">SEWER DRAIN CLEANING, MAINTENANCE, TRENCHLESS PIPE INSTALLS</textPath></text>
    </svg>
  </section>

  <!-- Contact side -->
  <section class="card card--contact">
    <svg width="520" height="297" viewBox="0 0 520 297" aria-label="Card back with contact details">
      <defs>
        <linearGradient id="paper-b" x1="0" y1="0" x2="0" y2="1">
          <stop offset="0" stop-color="var(--card-white)"/>
          <stop offset="1" stop-color="var(--card-shade)"/>
        </linearGradient>
        <linearGradient id="blue-fade" x1="0" y1="0" x2="0" y2="1">
          <stop offset="0" stop-color="var(--brand-blue)"/>
          <stop offset="1" stop-color="var(--deep-blue)"/>
        </linearGradient>
      </defs>
      <rect width="520" height="297" fill="url(#paper-b)"/>
      <path fill="var(--brand-red)" d="M0,297 L0,172 C90,196 200,182 290,144 C370,112 440,96 520,98 L520,297 Z"/>
      <path fill="var(--card-white)" d="M0,297 L0,189 C90,210 200,196 290,158 C370,127 440,111 520,112 L520,297 Z"/>
      <path fill="url(#blue-fade)" d="M0,297 L0,195 C90,215 200,201 290,164 C370,133 440,117 520,118 L520,297 Z"/>
      <g class="logo">
        <circle cx="398" cy="46" r="9" fill="var(--brand-red)"/>
        <text class="wordmark" x="160" y="64" font-size="34">Keystone</text>
        <text class="wordmark" x="196" y="100" font-size="34">Plumbing</text>
      </g>
      <g class="person">
        <text class="person-name" x="175" y="244" text-anchor="middle">MARCO ELLISON</text>
        <text class="person-role" x="175" y="262" text-anchor="middle">Director</text>
      </g>
      <line x1="258" y1="200" x2="258" y2="266" stroke="var(--text-white)" stroke-opacity="0.7" stroke-width="1"/>
      <g class="contacts">
        <g class="icon-phone" transform="translate(280,190)">
          <circle r="7" fill="none" stroke="var(--text-white)" stroke-width="1"/>
          <path d="M-3,-2 Q0,-4 3,-2 L3,0 L1,0 L1,-1 L-1,-1 L-1,0 L-3,0 Z M-3,1 L3,1 L3,3 L-3,3 Z" fill="var(--text-white)"/>
        </g>
        <text class="contact-line" x="294" y="195">1300555019</text>
        <g class="icon-mail" transform="translate(280,216)">
          <circle r="7" fill="none" stroke="var(--text-white)" stroke-width="1"/>
          <rect x="-3.5" y="-2.5" width="7" height="5" fill="none" stroke="var(--text-white)" stroke-width="1"/>
          <path d="M-3.5,-2.5 L0,0.5 L3.5,-2.5" fill="none" stroke="var(--text-white)" stroke-width="1"/>
        </g>
        <text class="contact-line" x="294" y="221">enquiry@keystoneplumbing.com</text>
        <text class="contact-web" x="274" y="248">www.keystoneplumbing.com</text>
      </g>
    </svg>
  </section>

</main>
</body>
</html>
```